Belmont Ridge Business Card Design Project

We have recently rebranded and would like to design new business cards that incorporate the corporate logo - double sided cards with corporate logo on one side and contact details on the other

Target Market(s)

Sophisticated and high net worth investors and finance industry professionals

Industry/Entity Type

Funds Management

Contact Information for Business Card

The card should prominently feature the company name and logo. Other details will be standard contact details for each staff member - name, address, phone, email, website

Colors
0054AA
0677BA
7BADD7
CADEEF
E8F1F8

Requirements
Must have
• Double-sided design with one side prominently featuring the corporate logo and the other side with all standard contact details

```html
<!DOCTYPE html>
<html lang="en">
<head>
<meta charset="utf-8">
<title>Belmont Ridge – Business Card</title>
<link href="https://fonts.googleapis.com/css2?family=Cinzel:wght@400;600&family=Arimo:wght@400&display=swap" rel="stylesheet">
<style>
  :root {
    --navy: #21467a;
    --paper: #ffffff;
    --ink: #1c1c1c;
    --backdrop: #e9ecf0;
    --card-shadow: rgba(20, 30, 50, 0.22);
  }
  * { box-sizing: border-box; margin: 0; padding: 0; }
  html, body {
    width: 1200px;
    height: 1015px;
    overflow: hidden;
    background: var(--backdrop);
  }
  .sheet {
    position: relative;
    width: 1200px;
    height: 1015px;
  }
  .card {
    position: absolute;
    left: 320px;
    width: 560px;
    height: 320px;
    box-shadow: 0 10px 30px var(--card-shadow);
    overflow: hidden;
  }
  .card--front {
    top: 150px;
    background: var(--navy);
    display: flex;
    align-items: center;
    justify-content: center;
  }
  .front-wordmark {
    font-family: "Cinzel", serif;
    font-weight: 400;
    font-size: 46px;
    letter-spacing: 1px;
    color: var(--paper);
  }
  .card--back {
    top: 530px;
    background: var(--paper);
  }
  .accent-square {
    position: absolute;
    left: 0;
    top: 88px;
    width: 34px;
    height: 34px;
    background: var(--navy);
  }
  .contact {
    position: absolute;
    left: 52px;
    top: 62px;
    font-family: "Arimo", Arial, sans-serif;
    color: var(--ink);
  }
  .contact__name {
    font-family: "Cinzel", serif;
    font-weight: 400;
    font-size: 24px;
    color: var(--navy);
    line-height: 1;
  }
  .contact__role {
    font-size: 15px;
    margin-top: 4px;
  }
  .contact__list {
    list-style: none;
    margin-top: 22px;
    font-size: 15px;
    line-height: 21px;
  }
  .contact__list li {
    display: flex;
    align-items: center;
    gap: 7px;
  }
  .contact__list svg {
    width: 13px;
    height: 13px;
    fill: var(--navy);
    flex: none;
  }
  .contact__address {
    margin-top: 30px;
    margin-left: 20px;
    font-size: 15px;
    line-height: 19px;
    font-style: normal;
  }
  .back-wordmark {
    position: absolute;
    right: 34px;
    top: 64px;
    font-family: "Cinzel", serif;
    font-weight: 400;
    font-size: 28px;
    color: var(--navy);
  }
</style>
</head>
<body>
<main class="sheet">
  <section class="card card--front" aria-label="Card front">
    <h1 class="front-wordmark">Belmont Ridge</h1>
  </section>

  <section class="card card--back" aria-label="Card back">
    <div class="accent-square"></div>
    <div class="contact">
      <h2 class="contact__name">Daniel Hartley</h2>
      <p class="contact__role">Managing Director</p>
      <ul class="contact__list">
        <li>
          <svg viewBox="0 0 16 16" aria-hidden="true"><path d="M3.6 1.2l2.3 2.6-1.2 1.8c.9 2 2.5 3.6 4.5 4.6l1.8-1.2 2.6 2.3-1.5 2.4C6.9 13.4 2.6 9.1 1.3 3l2.3-1.8z"/></svg>
          061-482 390 715
        </li>
        <li>
          <svg viewBox="0 0 16 16" aria-hidden="true"><path d="M1 3h14v10H1z M1.8 3.8L8 8.6l6.2-4.8" stroke="#fff" stroke-width="1"/></svg>
          hello@belmontridge.com
        </li>
        <li>
          <svg viewBox="0 0 16 16" aria-hidden="true"><circle cx="8" cy="8" r="7"/><path d="M1 8h14M8 1c-3 3-3 11 0 14M8 1c3 3 3 11 0 14" stroke="#fff" stroke-width="1" fill="none"/></svg>
          www.belmontridge.com
        </li>
      </ul>
      <address class="contact__address">
        18, Kestrel Lane, Suite 4<br>
        30217, Northbay
      </address>
    </div>
    <p class="back-wordmark">Belmont Ridge</p>
  </section>
</main>
</body>
</html>
```